Business Card design for law firm = Brightvale Australia

We are seeking a new design for our business cards.
We are keeping our logo, which is attached.
We need space for
Name
Title
Address is , which is
Level 7
214 Marlowe Street
Sydney NSW 2047
Phone :
Mobile :
Fax :
Email :
DX :
website www.brightvale-example.com.au

Industry/Entity Type

Law Firm / Banking and Finance

Contact Information for Business Card

We are seeking a new design for our business cards. We are keeping our logo. We need space for Name Title Address is Level 7 214 Marlowe Street Sydney NSW 2047 Phone Mobile Fax Email DX website www.brightvale-example.com.au

Colors
0054AA
0677BA
7BADD7
CADEEF
E8F1F8

Requirements
Must have
• see our website for general feel www.brightvale-example.com.au

```html
<!DOCTYPE html>
<html lang="en">
<head>
<meta charset="utf-8">
<title>Brightvale Australia – Business Card</title>
<link href="https://fonts.googleapis.com/css2?family=EB+Garamond:wght@400&family=Open+Sans:wght@400&display=swap" rel="stylesheet">
<style>
  :root {
    --backdrop: #2d2d2f;
    --card-dark: #1c1d1f;
    --card-light: #2a2b2e;
    --brand-navy: #2d4a9b;
    --brand-cyan: #1596c8;
    --tab-blue: #0a86c4;
    --text-light: #e6e6e6;
  }
  * { margin: 0; padding: 0; box-sizing: border-box; }
  html, body { width: 1200px; height: 1138px; overflow: hidden; }
  body {
    position: relative;
    background: var(--backdrop);
    font-family: "EB Garamond", Georgia, serif;
  }
  .card {
    position: absolute;
    border-radius: 20px;
    overflow: hidden;
    background: linear-gradient(160deg, var(--card-dark) 40%, var(--card-light) 100%);
    box-shadow: 0 6px 14px rgba(0,0,0,0.45);
  }
  .card--front { left: 272px; top: 184px; width: 622px; height: 376px; }
  .card--back  { left: 274px; top: 606px; width: 619px; height: 375px; }

  .company-name {
    position: absolute;
    color: var(--text-light);
    font-weight: 400;
    line-height: 1;
    white-space: nowrap;
  }
  .card--front .company-name { left: 0; width: 100%; text-align: center; top: 140px; font-size: 52px; }
  .card--front .tagline {
    position: absolute; left: 0; width: 100%; text-align: center; top: 212px;
    font-family: "Open Sans", Arial, sans-serif; font-size: 18px; letter-spacing: 1.5px;
    color: var(--brand-cyan);
  }
  .card--front .web-spaced {
    position: absolute; left: 0; width: 100%; text-align: center; top: 334px;
    font-size: 15px; letter-spacing: 7px; color: var(--text-light);
  }
  .card--front .accent-bar {
    position: absolute; left: 142px; bottom: 0; width: 340px; height: 8px;
    background: var(--brand-navy);
  }

  .card--back .company-name { left: 330px; top: 96px; font-size: 50px; }
  .person { position: absolute; left: 31px; top: 74px; }
  .person__name { font-size: 27px; color: var(--brand-navy); line-height: 1.1; }
  .person__title { font-size: 17px; color: var(--text-light); line-height: 1.2; }
  .address {
    position: absolute; left: 32px; top: 208px;
    font-size: 16.5px; line-height: 21px; color: var(--text-light);
  }
  .contacts { position: absolute; left: 32px; top: 260px; list-style: none; }
  .contacts li {
    display: flex; align-items: center; height: 20px;
    font-size: 16.5px; color: var(--text-light);
  }
  .contacts svg { width: 14px; height: 14px; margin-right: 17px; fill: var(--brand-cyan); }
  .tagline-tab {
    position: absolute; left: 280px; bottom: 0; width: 339px; height: 46px;
    background: var(--tab-blue);
    clip-path: polygon(22px 0, 100% 0, 100% 100%, 0 100%);
    display: flex; align-items: center; justify-content: center; padding-left: 24px;
    font-family: "Open Sans", Arial, sans-serif; font-size: 16px; letter-spacing: 1.2px;
    color: #ffffff;
  }
</style>
</head>
<body>
  <section class="card card--front">
    <div class="company-name">Brightvale</div>
    <div class="tagline">strategic legal outsourcing</div>
    <div class="web-spaced">www.brightvale-example.com.au</div>
    <div class="accent-bar"></div>
  </section>

  <section class="card card--back">
    <div class="person">
      <div class="person__name">Sam Hartley</div>
      <div class="person__title">Managing Director</div>
    </div>
    <div class="company-name">Brightvale</div>
    <div class="address">Level 7 214 Marlowe St<br>Sydney NSW 2047</div>
    <ul class="contacts">
      <li><svg viewBox="0 0 16 16" aria-hidden="true"><path d="M1 6c0-2 3-4 7-4s7 2 7 4v1h-4V5.5C10 5 9 5 8 5s-2 0-3 .5V7H1zM3 8h10l1 6H2z"/></svg>02 9555 0148</li>
      <li><svg viewBox="0 0 16 16" aria-hidden="true"><path d="M4 1h8v4H4zM1 6h14v6h-3v3H4v-3H1zM5 10v4h6v-4z"/></svg>02 9555 0149</li>
      <li><svg viewBox="0 0 16 16" aria-hidden="true"><path d="M1 3h14v10H1zM2 4l6 5 6-5v1L8 10 2 5z" fill-rule="evenodd"/></svg>sam.hartley@brightvale-example.com.au</li>
      <li><svg viewBox="0 0 16 16" aria-hidden="true"><circle cx="8" cy="8" r="6.5" fill="none" stroke="#1596c8" stroke-width="1.3"/><path d="M1.5 8h13M8 1.5c-2.5 3-2.5 10 0 13M8 1.5c2.5 3 2.5 10 0 13" fill="none" stroke="#1596c8" stroke-width="1.1"/></svg>www.brightvale-example.com.au</li>
    </ul>
    <div class="tagline-tab">strategic legal outsourcing</div>
  </section>
</body>
</html>
```